BMR Going Cashless

Hello,
We are a medical office looking to get a flyer created to promote to our patients we will be going "Cashless." Our tagline will be "Cash-Less is Stress-Less"

"Starting in July, to offer you the fastest and most convenient service, we are transitioning to a cashless system. You can now enjoy faster checkout times and greater security with card and contactless payments. More info to come."

I've added two other flyers as sample designs we've used.

Please include logo, addresses, website, phone number

Files to include jpeg, png, pdf (under 5mb), Facebook and Instagram sizing.

Thank you,
Lowen

```html
<!DOCTYPE html>
<html lang="en">
<head>
<meta charset="utf-8">
<title>BMR – Cash-Less is Stress-Less</title>
<link rel="stylesheet" href="https://fonts.googleapis.com/css2?family=Bebas+Neue&family=Mr+Dafoe&family=Montserrat:wght@700;800&family=Poppins:wght@300;400;500;600;700&display=swap">
<style>
:root{
  --board:#c4c4c4;
  --teal:#57c0a6;
  --teal-deep:#3fae93;
  --orange:#f47c45;
  --ink:#2a2a2a;
  --panel:#2d2d2d;
  --card-dark:#2b2b2b;
  --light:#ececec;
  --white:#ffffff;
  --label:#3c3c3c;
}
*{margin:0;padding:0;box-sizing:border-box}
html,body{width:1200px;height:2548px;overflow:hidden;background:var(--board)}
.stage{position:absolute;left:0;top:0;width:1213px;height:2576px;transform:scale(.9893);transform-origin:0 0;font-family:"Poppins",sans-serif}
.abs{position:absolute}
.size-label{position:absolute;left:0;width:1200px;text-align:center;font:400 30px "Poppins",sans-serif;color:var(--label);letter-spacing:.5px}

/* shared */
.script{font-family:"Mr Dafoe",cursive;line-height:1;white-space:nowrap}
.condensed{font-family:"Bebas Neue",sans-serif;line-height:1;white-space:nowrap}
.pill{background:var(--orange);color:var(--white);font-weight:600;text-align:center;border-radius:8px;letter-spacing:4px;box-shadow:0 0 0 3px rgba(255,255,255,.7)}
.brand{display:flex;align-items:center;gap:10px;font-family:"Poppins",sans-serif;font-weight:700;color:var(--orange)}
.brand-dot{border-radius:50%;background:var(--teal)}
.office{position:absolute;background:var(--card-dark);border-radius:6px;text-align:center;color:var(--white)}
.office-title{color:var(--teal);font-weight:700}
.office-pin{position:absolute;left:50%;transform:translateX(-50%)}
.web-bar{position:absolute;background:var(--orange);color:var(--white);font-family:"Poppins",sans-serif;font-weight:500}
.web-bar b{font-weight:700}
.photo{position:absolute}

/* square post */
.post-square{position:absolute;left:268px;top:143px;width:676px;height:752px;background:var(--white);overflow:hidden;box-shadow:10px 14px 18px rgba(0,0,0,.25)}
/* tall poster */
.post-tall{position:absolute;left:240px;top:1070px;width:741px;height:1318px;background:var(--panel);overflow:hidden;box-shadow:10px 14px 18px rgba(0,0,0,.25)}
</style>
</head>
<body>
<div class="stage">

  <!-- Square social post -->
  <section class="post-square">
    <svg class="abs" style="left:0;top:0" width="676" height="752" viewBox="0 0 676 752">
      <defs>
        <linearGradient id="bgFade" x1="0" y1="0" x2="1" y2="1">
          <stop offset="0" stop-color="#f4f4f4"/><stop offset="1" stop-color="#dadada"/>
        </linearGradient>
      </defs>
      <rect x="440" y="0" width="236" height="330" fill="url(#bgFade)"/>
      <path d="M0 0 H497 C560 140 540 330 380 410 C280 455 120 460 0 430 Z" fill="var(--teal)"/>
    </svg>
    <div class="photo" role="img" aria-label="Card payment terminal with floating bank cards and a smartphone showing a payment confirmation" style="left:300px;top:147px;width:372px;height:350px;background:radial-gradient(ellipse 50% 50% at 50% 55%,#2c3a55 0%,#1b2333 60%,rgba(27,35,51,0) 100%)"></div>

    <div class="abs script" style="left:30px;top:58px;font-size:88px;color:var(--ink)">Cash-Less</div>
    <div class="abs condensed" style="left:34px;top:150px;font-size:72px;color:var(--white)">IS STRESS-LESS</div>
    <div class="abs pill" style="left:36px;top:238px;width:170px;height:32px;font-size:23px;line-height:32px">STARTING</div>
    <div class="abs" style="left:34px;top:278px;font:800 54px 'Montserrat',sans-serif;color:var(--white)">IN JULY</div>
    <p class="abs" style="left:35px;top:346px;width:262px;font-size:14px;line-height:19px;color:var(--ink);font-weight:500">To offer you the fastest and most convenient service, we are transitioning to a cashless system</p>

    <p class="abs" style="left:35px;top:467px;font-size:19px;font-weight:300;color:var(--ink)">Now you can enjoy</p>
    <p class="abs" style="left:35px;top:491px;width:310px;font-size:19px;line-height:23px;font-weight:700;color:var(--teal)">faster checkout times and greater security with card and</p>
    <p class="abs" style="left:35px;top:545px;font:700 italic 28px 'Poppins',sans-serif;color:var(--orange);letter-spacing:-.5px">CONTACTLESS PAYMENTS</p>
    <p class="abs" style="left:35px;top:588px;font-size:13px;font-weight:600;letter-spacing:4px;color:var(--ink)">MORE INFO TO COME....</p>

    <div class="abs brand" style="left:430px;top:538px;font-size:44px">
      <span class="brand-dot" style="width:34px;height:34px"></span>BMR
    </div>

    <p class="abs" style="left:440px;top:622px;font-size:14px;font-weight:600;letter-spacing:4px;color:var(--teal)">CONTACT US TODAY</p>
    <svg class="abs" style="left:438px;top:648px" width="28" height="28" viewBox="0 0 28 28" aria-hidden="true">
      <circle cx="14" cy="14" r="12.5" fill="none" stroke="var(--orange)" stroke-width="2.5"/>
      <path d="M9 8c1-1 2-1 3 0l1.5 2.5c.4.8 0 1.5-.6 2l-.8.6c.8 1.8 2 3 3.8 3.8l.6-.8c.5-.6 1.2-1 2-.6L21 17c1 1 1 2 0 3-2 2-5 1-8-2s-4-7-4-10z" fill="var(--orange)"/>
    </svg>
    <p class="abs" style="left:470px;top:644px;font-size:27px;font-weight:600;color:var(--ink)">(555)014-0192</p>
    <div class="web-bar" style="left:438px;top:685px;width:238px;height:26px;font-size:15px;line-height:26px;padding-left:14px;letter-spacing:3px;border-radius:6px 0 0 6px">www.<b>bmrclinic</b>.com</div>

    <div class="office" style="left:34px;top:636px;width:127px;height:74px">
      <svg class="office-pin" style="top:-8px" width="16" height="16" viewBox="0 0 16 16" aria-hidden="true"><circle cx="8" cy="8" r="8" fill="var(--orange)"/><path d="M8 3.5a3 3 0 0 0-3 3c0 2 3 5.5 3 5.5s3-3.5 3-5.5a3 3 0 0 0-3-3z" fill="#fff"/><circle cx="8" cy="6.5" r="1.1" fill="var(--orange)"/></svg>
      <p class="office-title" style="font-size:12px;margin-top:14px">Northgate Office</p>
      <p style="font-size:8.5px;line-height:11px;margin-top:2px">88 Maple Grove<br>Dr.Suite110 Northgate,<br>ST10021</p>
    </div>
    <div class="office" style="left:166px;top:636px;width:127px;height:74px">
      <svg class="office-pin" style="top:-8px" width="16" height="16" viewBox="0 0 16 16" aria-hidden="true"><circle cx="8" cy="8" r="8" fill="var(--orange)"/><path d="M8 3.5a3 3 0 0 0-3 3c0 2 3 5.5 3 5.5s3-3.5 3-5.5a3 3 0 0 0-3-3z" fill="#fff"/><circle cx="8" cy="6.5" r="1.1" fill="var(--orange)"/></svg>
      <p class="office-title" style="font-size:12px;margin-top:14px">Riverside Office</p>
      <p style="font-size:8.5px;line-height:11px;margin-top:2px">45 Willow Lane<br>Riverside,ST10034</p>
    </div>
    <div class="office" style="left:298px;top:636px;width:127px;height:74px">
      <svg class="office-pin" style="top:-8px" width="16" height="16" viewBox="0 0 16 16" aria-hidden="true"><circle cx="8" cy="8" r="8" fill="var(--orange)"/><path d="M8 3.5a3 3 0 0 0-3 3c0 2 3 5.5 3 5.5s3-3.5 3-5.5a3 3 0 0 0-3-3z" fill="#fff"/><circle cx="8" cy="6.5" r="1.1" fill="var(--orange)"/></svg>
      <p class="office-title" style="font-size:12px;margin-top:14px">Hillcrest Office</p>
      <p style="font-size:8.5px;line-height:11px;margin-top:2px">2100 Cedar Park<br>Blvd.Suite 204 Hillcrest,<br>ST10047</p>
    </div>
  </section>
  <p class="size-label" style="top:950px;width:1213px">1080 X 1080</p>

  <!-- Tall story poster -->
  <section class="post-tall">
    <svg class="abs" style="left:0;top:0" width="741" height="1318" viewBox="0 0 741 1318">
      <path d="M0 800 C180 690 560 690 741 800 V1318 H0 Z" fill="var(--teal)"/>
      <path d="M0 830 C180 715 560 715 741 830 V1318 H0 Z" fill="var(--light)"/>
    </svg>

    <div class="abs brand" style="left:0;width:741px;justify-content:center;top:40px;font-size:64px">
      <span class="brand-dot" style="width:46px;height:46px"></span>BMR
    </div>

    <div class="abs script" style="left:0;width:741px;text-align:center;top:168px;font-size:145px;color:var(--teal)">Cash-Less</div>
    <div class="abs condensed" style="left:0;width:741px;text-align:center;top:298px;font-size:124px;color:var(--orange)">IS STRESS-LESS</div>

    <div class="photo" role="img" aria-label="Card payment terminal with floating bank cards and a smartphone showing a payment confirmation" style="left:88px;top:420px;width:560px;height:420px;background:radial-gradient(ellipse 50% 50% at 50% 55%,#2f3d5a 0%,#1c2434 60%,rgba(28,36,52,0) 100%)"></div>

    <div class="abs pill" style="left:40px;top:878px;width:206px;height:32px;font-size:28px;line-height:32px">STARTING</div>
    <div class="abs" style="left:36px;top:918px;font:800 64px 'Montserrat',sans-serif;color:var(--teal)">IN JULY</div>
    <p class="abs" style="left:36px;top:1003px;width:330px;font-size:18.5px;line-height:22px;color:var(--ink)">To offer you the fastest and most convenient service, we are transitioning to a cashless system</p>

    <div class="abs" style="left:370px;top:880px;height:190px;border-left:2px dashed #777"></div>

    <p class="abs" style="left:398px;top:873px;font:700 28px 'Montserrat',sans-serif;color:var(--teal);white-space:nowrap">YOU CAN <span style="color:var(--orange)">NOW ENJOY</span></p>
    <ul class="abs" style="left:402px;top:926px;list-style:none;font-size:22px;line-height:35px;color:var(--ink)">
      <li><svg width="15" height="15" viewBox="0 0 16 16" aria-hidden="true" style="margin-right:8px"><circle cx="8" cy="8" r="8" fill="var(--orange)"/><path d="M4.5 8.3l2.3 2.2 4.7-4.8" fill="none" stroke="#fff" stroke-width="2"/></svg>Faster checkout times</li>
      <li><svg width="15" height="15" viewBox="0 0 16 16" aria-hidden="true" style="margin-right:8px"><circle cx="8" cy="8" r="8" fill="var(--orange)"/><path d="M4.5 8.3l2.3 2.2 4.7-4.8" fill="none" stroke="#fff" stroke-width="2"/></svg>Greater security with card</li>
      <li><svg width="15" height="15" viewBox="0 0 16 16" aria-hidden="true" style="margin-right:8px"><circle cx="8" cy="8" r="8" fill="var(--orange)"/><path d="M4.5 8.3l2.3 2.2 4.7-4.8" fill="none" stroke="#fff" stroke-width="2"/></svg>Contactless payments</li>
    </ul>
    <p class="abs" style="left:402px;top:1048px;font-size:15px;font-weight:600;letter-spacing:5px;color:var(--ink)">MORE INFO TO COME....</p>

    <div class="office" style="left:38px;top:1110px;width:217px;height:114px">
      <svg class="office-pin" style="top:-12px" width="24" height="24" viewBox="0 0 16 16" aria-hidden="true"><circle cx="8" cy="8" r="8" fill="var(--orange)"/><path d="M8 3.5a3 3 0 0 0-3 3c0 2 3 5.5 3 5.5s3-3.5 3-5.5a3 3 0 0 0-3-3z" fill="#fff"/><circle cx="8" cy="6.5" r="1.1" fill="var(--orange)"/></svg>
      <p class="office-title" style="font-size:20px;margin-top:22px">Northgate Office</p>
      <p style="font-size:15px;line-height:18px;margin-top:2px">88 Maple Grove<br>Dr.Suite110 Northgate,<br>ST10021</p>
    </div>
    <div class="office" style="left:263px;top:1110px;width:217px;height:114px">
      <svg class="office-pin" style="top:-12px" width="24" height="24" viewBox="0 0 16 16" aria-hidden="true"><circle cx="8" cy="8" r="8" fill="var(--orange)"/><path d="M8 3.5a3 3 0 0 0-3 3c0 2 3 5.5 3 5.5s3-3.5 3-5.5a3 3 0 0 0-3-3z" fill="#fff"/><circle cx="8" cy="6.5" r="1.1" fill="var(--orange)"/></svg>
      <p class="office-title" style="font-size:20px;margin-top:22px">Riverside Office</p>
      <p style="font-size:15px;line-height:18px;margin-top:4px">45 Willow Lane<br>Riverside,ST10034</p>
    </div>
    <div class="office" style="left:488px;top:1110px;width:217px;height:114px">
      <svg class="office-pin" style="top:-12px" width="24" height="24" viewBox="0 0 16 16" aria-hidden="true"><circle cx="8" cy="8" r="8" fill="var(--orange)"/><path d="M8 3.5a3 3 0 0 0-3 3c0 2 3 5.5 3 5.5s3-3.5 3-5.5a3 3 0 0 0-3-3z" fill="#fff"/><circle cx="8" cy="6.5" r="1.1" fill="var(--orange)"/></svg>
      <p class="office-title" style="font-size:20px;margin-top:22px">Hillcrest Office</p>
      <p style="font-size:15px;line-height:18px;margin-top:4px">2100 Cedar Park<br>Blvd.Suite 204 Hillcrest,<br>ST10047</p>
    </div>

    <svg class="abs" style="left:38px;top:1240px" width="42" height="42" viewBox="0 0 28 28" aria-hidden="true">
      <circle cx="14" cy="14" r="12.5" fill="none" stroke="var(--orange)" stroke-width="2.5"/>
      <path d="M9 8c1-1 2-1 3 0l1.5 2.5c.4.8 0 1.5-.6 2l-.8.6c.8 1.8 2 3 3.8 3.8l.6-.8c.5-.6 1.2-1 2-.6L21 17c1 1 1 2 0 3-2 2-5 1-8-2s-4-7-4-10z" fill="var(--orange)"/>
    </svg>
    <p class="abs" style="left:88px;top:1234px;font-size:37px;font-weight:600;color:var(--ink)">(555)014-0192</p>
    <div class="web-bar" style="left:380px;top:1239px;width:361px;height:34px;font-size:21px;line-height:34px;padding-left:20px;letter-spacing:4px;border-radius:17px 0 0 17px">www.<b>bmrclinic</b>.com</div>
  </section>
  <p class="size-label" style="top:2460px;width:1213px">1920 X 1080</p>

</div>
</body>
</html>
```